Family business needs stationery redesign with new logo

Family owned company, established in 1987 wanting a brand 'refresh'. We are an electrical, refrigeration and construction company based in the Barkly Region Northern Territory, Australia. We have a new logo we would like to use which is uploaded along with our current letterhead and email signature. We are also dropping the word 'contractors' so please do not include this on any designs. Please note also, the 'orange' color used in our logo and designs should be Northern Territory red ochre which is as follows:

RGB (Hex): #C75B12
PantoneĀ® 159 C
CMYK: 1 / 74 / 100 / 7

We are needing our stationery redesigned using our new logo. Please include letterheads, business cards, envelopes, and email signatures.

We currently use our business letterheads for quotations, invoices, letters, HR matters, and internal memos.

We also need a separate simplified letterhead for internal paperwork such as employee leave forms, meeting agendas, and meeting minutes etc.

Reason: Needing more submissions of full package designs. We are wanting all our stationery, including business cards, letterheads, email signatures, envelopes, etc to be cohesive. We also require ALL the information, as supplied on our template letterhead, to be included on the new letterhead designs. including electrical license no.etc Thank you, R&W

Reason: needing more time as work has got in the way of looking over designs. A lot of designs not meeting the brief/criteria.

Industry/Entity Type

Business

Colors
0355a3
f37122

Requirements
Must have
• The 'orange' color used in the designs should be Northern Territory red ochre which is as follows:
• RGB (Hex): #C75B12
• PantoneĀ® 159 C
• CMYK: 1 / 74 / 100 / 7
• ***MUST INCLUDE ALL INFORMATION THAT IS ON OUR CURRENT LETTERHEAD***
Should not have
• Please do not include the word 'contractors'

```html
<!DOCTYPE html>
<html lang="en">
<head>
<meta charset="UTF-8">
<title>R&amp;W Business Card</title>
<link href="https://fonts.googleapis.com/css2?family=Arimo:wght@400;700&display=swap" rel="stylesheet">
<style>
  :root {
    --page-bg: #d8d5d1;
    --navy-light: #263266;
    --navy-dark: #0c112c;
    --ochre: #c75b12;
    --frost: #e3e6ea;
    --frost-shade: #cfd4db;
    --text-light: #f2f3f7;
    --logo-navy: #121a45;
  }
  * { margin: 0; padding: 0; box-sizing: border-box; }
  html, body {
    width: 1200px;
    height: 969px;
    overflow: hidden;
    background: var(--page-bg);
    font-family: "Arimo", Arial, sans-serif;
  }
  .business-card {
    position: absolute;
    left: 100px;
    top: 199px;
    width: 1000px;
    height: 571px;
    border-radius: 24px;
    overflow: hidden;
    background: linear-gradient(135deg, var(--frost) 0%, var(--frost-shade) 100%);
    box-shadow: 0 10px 30px rgba(0,0,0,0.18);
  }
  .card-shapes {
    position: absolute;
    inset: 0;
    width: 100%;
    height: 100%;
  }
  .contact-block {
    position: absolute;
    left: 46px;
    top: 128px;
    color: var(--text-light);
  }
  .person-name {
    font-size: 33px;
    font-weight: 700;
    letter-spacing: 1px;
    color: var(--ochre);
    line-height: 40px;
  }
  .person-title {
    font-size: 25px;
    line-height: 36px;
    margin-bottom: 22px;
  }
  .address {
    font-size: 25px;
    line-height: 32px;
    margin-bottom: 22px;
  }
  .contact-list { list-style: none; }
  .contact-list li {
    display: flex;
    align-items: center;
    font-size: 25px;
    line-height: 38px;
  }
  .contact-list svg {
    width: 24px;
    height: 24px;
    margin-right: 14px;
    fill: var(--ochre);
    flex-shrink: 0;
  }
  .brand-name {
    position: absolute;
    left: 728px;
    top: 301px;
    transform: translate(-50%, -50%);
    font-size: 100px;
    font-weight: 700;
    color: var(--logo-navy);
    letter-spacing: 2px;
  }
</style>
</head>
<body>
  <div class="business-card">
    <svg class="card-shapes" viewBox="0 0 1000 571" preserveAspectRatio="none" aria-hidden="true">
      <defs>
        <linearGradient id="navyPanel" x1="0" y1="0" x2="1" y2="1">
          <stop offset="0" stop-color="#1c2558"/>
          <stop offset="0.45" stop-color="#263266"/>
          <stop offset="1" stop-color="#0c112c"/>
        </linearGradient>
      </defs>
      <path d="M0 0 H770 C560 40 380 170 395 305 C410 440 600 535 830 571 H0 Z" fill="url(#navyPanel)"/>
      <path d="M786 0 C572 42 392 172 407 305 C422 438 612 532 850 571" fill="none" stroke="#c75b12" stroke-width="5"/>
    </svg>

    <div class="contact-block">
      <p class="person-name">DANA WHITLOW</p>
      <p class="person-title">CEO/Founder</p>
      <p class="address">412 Ochre Street<br>Tennant Creek, NT 0860</p>
      <ul class="contact-list">
        <li>
          <svg viewBox="0 0 24 24"><path d="M6.6 10.8a15.1 15.1 0 0 0 6.6 6.6l2.2-2.2a1 1 0 0 1 1-.25 11.4 11.4 0 0 0 3.6.57 1 1 0 0 1 1 1V20a1 1 0 0 1-1 1A17 17 0 0 1 3 4a1 1 0 0 1 1-1h3.5a1 1 0 0 1 1 1c0 1.25.2 2.45.57 3.6a1 1 0 0 1-.25 1z"/></svg>
          555 210 4871
        </li>
        <li>
          <svg viewBox="0 0 24 24"><path d="M6 2h12v5H6zM3 8h18a2 2 0 0 1 2 2v7h-4v5H5v-5H1v-7a2 2 0 0 1 2-2zm4 9v3h10v-3z"/></svg>
          555 302 6695
        </li>
        <li>
          <svg viewBox="0 0 24 24"><path d="M2 5h20v14H2zm2 2v.4l8 5 8-5V7zm0 2.8V17h16V9.8l-8 5z"/></svg>
          hello@rwbuild.example
        </li>
        <li>
          <svg viewBox="0 0 24 24"><path d="M12 2a10 10 0 1 0 0 20 10 10 0 0 0 0-20zm6.9 9h-3a15 15 0 0 0-1.4-6A8 8 0 0 1 18.9 11zM12 4.1A13 13 0 0 1 13.9 11h-3.8A13 13 0 0 1 12 4.1zM9.5 5a15 15 0 0 0-1.4 6h-3A8 8 0 0 1 9.5 5zM5.1 13h3a15 15 0 0 0 1.4 6 8 8 0 0 1-4.4-6zm6.9 6.9A13 13 0 0 1 10.1 13h3.8a13 13 0 0 1-1.9 6.9zm2.5-.9a15 15 0 0 0 1.4-6h3a8 8 0 0 1-4.4 6z"/></svg>
          www.rwbuild.example
        </li>
      </ul>
    </div>

    <p class="brand-name">R&amp;W</p>
  </div>
</body>
</html>
```